YouTube Thumbnail for Educational Video About WW2

Please design a bespoke thumbnail for a YouTube video with the following title:
"Nobody Expected Such An Odd Clash Ever"
The video is about the battle for Castle Vornholm, which was a small battle that happened during WW2, in which the Germans fought against themselves for control of Castle Vornholm.
The thumbnail should be 1920x1080 pixels

```html
<!DOCTYPE html>
<html lang="en">
<head>
<meta charset="utf-8">
<title>Thumbnail – Nobody Expected Such An Odd Clash Ever</title>
<link rel="stylesheet" href="https://fonts.googleapis.com/css2?family=Anton&family=Roboto:wght@400;500;700&family=Roboto+Condensed:wght@400;700&display=swap">
<style>
  :root {
    --stage-grey: #c2c2c2;
    --page-white: #ffffff;
    --title-white: #ffffff;
    --title-red: #ec1019;
    --app-red: #d62727;
    --button-red: #f04848;
    --device-black: #111111;
    --screen-light: #ececec;
    --banner-grey: #bdbdbd;
    --text-dark: #1b1b1b;
    --text-grey: #8a8a8a;
    --player-bar: #3a3a3a;
    --panel-white: #f8f8f8;
    --engraving-light: #b9b9b9;
    --engraving-mid: #6e6e6e;
    --engraving-dark: #262626;
  }
  * { box-sizing: border-box; }
  html, body {
    margin: 0; padding: 0;
    width: 812px; height: 1200px;
    overflow: hidden;
    background: var(--page-white);
    font-family: "Roboto", Arial, sans-serif;
  }
  .canvas { position: relative; width: 812px; height: 1200px; }
  .stage { position: absolute; left: 0; top: 0; width: 812px; height: 632px; background: var(--stage-grey); }

  /* shared artwork + title */
  .artwork {
    position: absolute; inset: 0;
    background:
      radial-gradient(ellipse 60% 50% at 85% 30%, var(--engraving-light), transparent 70%),
      radial-gradient(ellipse 45% 40% at 45% 35%, var(--engraving-mid), transparent 75%),
      linear-gradient(180deg, #8a8a8a 0%, #5a5a5a 45%, var(--engraving-dark) 100%);
  }
  .art-title {
    position: absolute; left: 0; right: 0; margin: 0;
    text-align: center;
    font-family: "Anton", "Oswald", sans-serif;
    font-weight: 400;
    text-transform: uppercase;
    font-size: var(--size);
    line-height: var(--lead);
    bottom: var(--bottom);
    letter-spacing: 0.2px;
  }
  .art-title span { display: block; color: var(--title-white); text-shadow: 0 2px 6px rgba(0,0,0,.55); }
  .art-title .accent { color: var(--title-red); }

  /* phone */
  .phone {
    position: absolute; left: 64px; top: 67px; width: 247px; height: 503px;
    background: var(--device-black); border-radius: 36px;
    box-shadow: 10px 14px 30px rgba(0,0,0,.35);
  }
  .phone__screen {
    position: absolute; left: 10px; top: 8px; width: 227px; height: 482px;
    border-radius: 28px 28px 22px 22px; overflow: hidden; background: var(--screen-light);
  }
  .appbar { position: absolute; left: 0; top: 0; width: 100%; height: 73px; background: var(--app-red); color: #fff; }
  .appbar__notch { position: absolute; left: 52px; top: 0; width: 122px; height: 14px; background: var(--device-black); border-radius: 0 0 12px 12px; }
  .appbar__time { position: absolute; left: 18px; top: 5px; font-size: 8px; font-weight: 700; }
  .appbar__status { position: absolute; right: 12px; top: 5px; }
  .appbar__toolbar { position: absolute; left: 0; top: 24px; width: 100%; height: 20px; }
  .appbar__title { position: absolute; left: 32px; top: 2px; font-size: 12px; font-weight: 700; }
  .appbar__tabs { position: absolute; left: 0; top: 55px; width: 100%; font-size: 7.5px; font-weight: 700; }
  .appbar__tabs span { position: absolute; }
  .appbar__tab-line { position: absolute; left: 0; bottom: 0; width: 60px; height: 2px; background: #fff; }
  .banner { position: absolute; left: 0; top: 73px; width: 100%; height: 64px; background: var(--banner-grey); }
  .channel { position: absolute; left: 0; top: 137px; width: 100%; height: 65px; }
  .channel__avatar { position: absolute; left: 9px; top: 6px; }
  .channel__name { position: absolute; left: 65px; top: 8px; font-size: 11px; font-weight: 700; color: var(--text-dark); }
  .channel__subs { position: absolute; left: 65px; top: 24px; font-size: 7.5px; color: #666; }
  .channel__subscribe { position: absolute; left: 65px; top: 37px; font-size: 8px; font-weight: 700; color: var(--app-red); }
  .feed-thumb { position: absolute; left: 0; width: 100%; overflow: hidden; }
  .feed-thumb--main { top: 202px; height: 129px; }
  .feed-thumb--next { top: 382px; height: 44px; }
  .feed-thumb__time { position: absolute; right: 6px; bottom: 3px; font-size: 6px; font-weight: 700; color: #fff; }
  .feed-info { position: absolute; left: 0; top: 331px; width: 100%; height: 51px; }
  .feed-info__avatar { position: absolute; left: 9px; top: 9px; }
  .feed-info__title { position: absolute; left: 38px; top: 8px; width: 185px; font-size: 7.5px; font-weight: 700; line-height: 9px; color: var(--text-dark); }
  .feed-info__meta { position: absolute; left: 38px; top: 30px; font-size: 6px; color: #444; word-spacing: 2px; }
  .bottom-nav { position: absolute; left: 0; top: 426px; width: 100%; height: 31px; background: #fff; font-size: 5px; color: #222; }
  .bottom-nav__item { position: absolute; top: 4px; width: 40px; margin-left: -20px; text-align: center; }
  .bottom-nav__item svg { display: block; margin: 0 auto 1px; }
  .system-nav { position: absolute; left: 0; top: 457px; width: 100%; height: 25px; background: var(--device-black); }

  /* desktop player */
  .player-card {
    position: absolute; left: 365px; top: 148px; width: 392px; height: 376px;
    background: var(--panel-white); border-radius: 16px;
    box-shadow: 0 6px 18px rgba(0,0,0,.12);
  }
  .player { position: absolute; left: 14px; top: 16px; width: 363px; height: 224px; border-radius: 4px; overflow: hidden; box-shadow: 0 4px 10px rgba(0,0,0,.3); }
  .player__video { position: absolute; left: 0; top: 0; width: 100%; height: 195px; overflow: hidden; }
  .player__controls { position: absolute; left: 0; top: 195px; width: 100%; height: 29px; background: var(--player-bar); }
  .player__progress { position: absolute; left: 7px; top: 3px; width: 348px; height: 3px; background: #fff; }
  .player__progress-fill { position: absolute; left: 0; top: 0; width: 160px; height: 3px; background: var(--button-red); }
  .player__progress-dot { position: absolute; left: 156px; top: -2px; width: 7px; height: 7px; border-radius: 50%; background: var(--button-red); }
  .video-meta__title { position: absolute; left: 14px; top: 248px; font-family: "Roboto Condensed", sans-serif; font-size: 11px; color: #333; }
  .video-meta__stats { position: absolute; left: 14px; top: 266px; font-size: 6.5px; color: #aaa; }
  .video-meta__actions { position: absolute; right: 16px; top: 265px; font-size: 6.5px; color: #999; display: flex; gap: 8px; align-items: center; }
  .video-meta__actions span { display: flex; align-items: center; gap: 2px; }
  .video-meta__divider { position: absolute; left: 16px; top: 286px; width: 360px; height: 1px; background: #ccc; }
  .uploader__avatar { position: absolute; left: 16px; top: 294px; }
  .uploader__name { position: absolute; left: 42px; top: 296px; font-family: "Roboto Condensed", sans-serif; font-size: 9px; color: #222; }
  .uploader__subs { position: absolute; left: 42px; top: 308px; font-size: 5.5px; color: #aaa; }
  .uploader__button { position: absolute; left: 305px; top: 296px; width: 72px; height: 22px; border-radius: 5px; background: var(--button-red); color: #fff; font-family: "Roboto Condensed", sans-serif; font-weight: 700; font-size: 9px; line-height: 22px; text-align: center; box-shadow: 0 2px 4px rgba(0,0,0,.2); }
  .uploader__about { position: absolute; left: 14px; top: 325px; width: 250px; font-size: 6px; line-height: 9px; color: #555; }

  /* final thumbnail */
  .thumbnail {
    position: absolute; left: 90px; top: 712px; width: 633px; height: 351px;
    overflow: hidden; box-shadow: 0 14px 50px rgba(0,0,0,.25);
  }
</style>
</head>
<body>
<main class="canvas">
  <section class="stage" aria-label="Thumbnail preview on mobile and desktop">

    <div class="phone">
      <div class="phone__screen">
        <header class="appbar">
          <div class="appbar__notch"></div>
          <span class="appbar__time">9:45</span>
          <svg class="appbar__status" width="36" height="8" viewBox="0 0 36 8" fill="#fff">
            <rect x="0" y="5" width="1.5" height="3"/><rect x="2.5" y="3.5" width="1.5" height="4.5"/><rect x="5" y="2" width="1.5" height="6"/><rect x="7.5" y="0.5" width="1.5" height="7.5"/>
            <path d="M12 3 a6 6 0 0 1 8 0 l-1 1 a4.5 4.5 0 0 0 -6 0z M14 5 a3 3 0 0 1 4 0 l-2 2z"/>
            <rect x="24" y="1.5" width="10" height="5" rx="1"/><rect x="34.3" y="3" width="1" height="2"/>
          </svg>
          <div class="appbar__toolbar">
            <svg style="position:absolute;left:9px;top:4px" width="12" height="10" viewBox="0 0 12 10" fill="none" stroke="#fff" stroke-width="1"><path d="M11 5H1M5 1L1 5l4 4"/></svg>
            <span class="appbar__title">Channel Name</span>
            <svg style="position:absolute;left:166px;top:4px" width="12" height="10" viewBox="0 0 12 10" fill="none" stroke="#fff" stroke-width="0.9"><path d="M1 3V1h10v8H6M1 6a3 3 0 0 1 3 3M1 8a1 1 0 0 1 1 1"/></svg>
            <svg style="position:absolute;left:189px;top:3px" width="11" height="11" viewBox="0 0 11 11" fill="none" stroke="#fff" stroke-width="1"><circle cx="4.5" cy="4.5" r="3.5"/><path d="M7 7l3.5 3.5"/></svg>
            <svg style="position:absolute;left:214px;top:4px" width="3" height="10" viewBox="0 0 3 10" fill="#fff"><circle cx="1.5" cy="1.5" r="1"/><circle cx="1.5" cy="5" r="1"/><circle cx="1.5" cy="8.5" r="1"/></svg>
          </div>
          <nav class="appbar__tabs">
            <span style="left:12px">HOME</span>
            <span style="left:62px">VIDEO</span>
            <span style="left:113px">PLAYLIST</span>
            <span style="left:169px">COMMUNITY</span>
          </nav>
          <div class="appbar__tab-line"></div>
        </header>

        <div class="banner">
          <svg style="position:absolute;left:98px;top:18px" width="32" height="26" viewBox="0 0 32 26" fill="#e6e6e6"><path d="M4 6h6l3-4h6l3 4h6a3 3 0 0 1 3 3v13a3 3 0 0 1-3 3H4a3 3 0 0 1-3-3V9a3 3 0 0 1 3-3z"/><circle cx="16" cy="15" r="6" fill="#bdbdbd"/><circle cx="16" cy="15" r="3.5" fill="#e6e6e6"/></svg>
        </div>

        <div class="channel">
          <svg class="channel__avatar" width="48" height="48" viewBox="0 0 48 48"><circle cx="24" cy="24" r="23" fill="none" stroke="#d62727" stroke-width="1.5"/><circle cx="24" cy="24" r="21" fill="#1b1b1b"/><circle cx="24" cy="18" r="6.5" fill="#fff"/><path d="M12 34a12 9 0 0 1 24 0z" fill="#fff"/></svg>
          <span class="channel__name">Channel Name</span>
          <span class="channel__subs">2,85M subscribers</span>
          <span class="channel__subscribe">SUBSCRIBE</span>
        </div>

        <div class="feed-thumb feed-thumb--main">
          <div class="artwork" role="img" aria-label="Black and white engraving of a damaged castle with soldiers in a trench"></div>
          <h2 class="art-title" style="--size:20px;--lead:18px;--bottom:14px">
            <span>Nobody Expected</span><span>Such An Odd</span><span class="accent">Clash Ever</span>
          </h2>
          <span class="feed-thumb__time">5.45</span>
        </div>

        <div class="feed-info">
          <svg class="feed-info__avatar" width="21" height="21" viewBox="0 0 21 21"><circle cx="10.5" cy="10.5" r="10" fill="#d62727"/><circle cx="10.5" cy="8" r="3.5" fill="#fff"/><path d="M4 16a6.5 5 0 0 1 13 0z" fill="#fff"/></svg>
          <div class="feed-info__title">LOREM IPSUM DOLOR SIT AMET,CONSE<br>CTETUR ADIPISCING ELIT,</div>
          <div class="feed-info__meta">Channel Name &nbsp; 325K views &nbsp; 1 day ago</div>
        </div>

        <div class="feed-thumb feed-thumb--next">
          <div class="artwork" role="img" aria-label="Black and white engraving of a damaged castle"></div>
        </div>

        <nav class="bottom-nav">
          <div class="bottom-nav__item" style="left:18px"><svg width="10" height="10" viewBox="0 0 10 10" fill="#222"><path d="M5 0.5L0.5 4.5V10h3.5V7h2v3h3.5V4.5z"/></svg>Home</div>
          <div class="bottom-nav__item" style="left:66px"><svg width="11" height="11" viewBox="0 0 11 11" fill="none" stroke="#222"><circle cx="5.5" cy="5.5" r="4.8"/><path d="M7.5 3.5L6.3 6.3 3.5 7.5 4.7 4.7z" fill="#222"/></svg>Explore</div>
          <div class="bottom-nav__item" style="left:113px;top:5px"><svg width="19" height="19" viewBox="0 0 19 19" fill="none" stroke="#222"><circle cx="9.5" cy="9.5" r="8.8"/><path d="M9.5 4.5v10M4.5 9.5h10"/></svg></div>
          <div class="bottom-nav__item" style="left:160px"><svg width="12" height="11" viewBox="0 0 12 11" fill="none" stroke="#222" stroke-width="0.9"><path d="M3 1h6M2 3h8"/><rect x="1" y="4.5" width="10" height="6"/><path d="M5 6v3l2.5-1.5z" fill="#222"/><circle cx="10.5" cy="1.5" r="1.5" fill="#d62727" stroke="none"/></svg>Subcription</div>
          <div class="bottom-nav__item" style="left:209px"><svg width="10" height="10" viewBox="0 0 10 10" fill="none" stroke="#222" stroke-width="0.9"><rect x="2.5" y="0.5" width="7" height="7"/><path d="M0.5 2.5v7h7"/><path d="M5 2.5v3l2.2-1.5z" fill="#222"/></svg>Library</div>
        </nav>

        <div class="system-nav">
          <svg width="227" height="25" viewBox="0 0 227 25" fill="none" stroke="#ddd" stroke-width="1"><path d="M69 8l-5 4.5 5 4.5z"/><circle cx="114" cy="12.5" r="4.2"/><rect x="159" y="8.5" width="8" height="8"/></svg>
        </div>
      </div>
    </div>

    <div class="player-card">
      <div class="player">
        <div class="player__video">
          <div class="artwork" role="img" aria-label="Black and white engraving of a damaged castle among trees, soldiers in a trench at left and mounted officers at right"></div>
          <h2 class="art-title" style="--size:34px;--lead:29px;--bottom:12px">
            <span>Nobody Expected</span><span>Such An Odd</span><span class="accent">Clash Ever</span>
          </h2>
        </div>
        <div class="player__controls">
          <div class="player__progress"><div class="player__progress-fill"></div><div class="player__progress-dot"></div></div>
          <svg style="position:absolute;left:7px;top:11px" width="50" height="12" viewBox="0 0 50 12" fill="#fff"><rect x="1" y="1" width="2.5" height="9"/><rect x="5.5" y="1" width="2.5" height="9"/><path d="M17 1l6 4.5-6 4.5z"/><rect x="23.5" y="1" width="1.8" height="9"/><path d="M34 3.5h2.5l3.5-3v11l-3.5-3H34z"/><path d="M41.5 3a4 4 0 0 1 0 5.5M43.5 1.5a6 6 0 0 1 0 8.5" fill="none" stroke="#fff" stroke-width="1"/></svg>
          <svg style="position:absolute;right:8px;top:11px" width="60" height="12" viewBox="0 0 60 12" fill="none" stroke="#fff" stroke-width="1.4"><circle cx="5" cy="6" r="2.5" fill="#fff"/><circle cx="5" cy="6" r="4.3" stroke-dasharray="2 1.4"/><rect x="16" y="1.5" width="10" height="9" rx="1.5"/><rect x="19.5" y="5" width="4" height="3" fill="#fff" stroke="none"/><rect x="32" y="2.5" width="11" height="7"/><path d="M49 4V1.5h2.5M56 1.5h2.5V4M58.5 8v2.5H56M51.5 10.5H49V8"/></svg>
        </div>
      </div>

      <div class="video-meta__title">Your video name is here</div>
      <div class="video-meta__stats">12.751 views &nbsp;Dec 1, 2020</div>
      <div class="video-meta__actions">
        <span><svg width="9" height="8" viewBox="0 0 9 8" fill="#999"><rect x="0" y="3" width="2" height="5"/><path d="M2.5 3L5 0c1 0 1.2.8 1 1.6L5.7 3H8.5l-.8 5H2.5z"/></svg>754</span>
        <span><svg width="9" height="8" viewBox="0 0 9 8" fill="#999"><rect x="7" y="0" width="2" height="5"/><path d="M6.5 5L4 8c-1 0-1.2-.8-1-1.6L3.3 5H.5l.8-5h5.2z"/></svg>18</span>
        <span><svg width="9" height="7" viewBox="0 0 9 7" fill="#999"><path d="M5 0l4 3.5L5 7V5C2.5 5 1 5.8 0 7c.5-3 2-5 5-5z"/></svg>SHARE</span>
        <span><svg width="9" height="7" viewBox="0 0 9 7" fill="#999"><rect x="0" y="0" width="5" height="1.2"/><rect x="0" y="2.5" width="5" height="1.2"/><rect x="0" y="5" width="3" height="1.2"/><path d="M6.5 3v4M4.5 5h4" stroke="#999" stroke-width="1.2"/></svg>SAVE</span>
        <span style="margin-left:8px;letter-spacing:-1px;font-weight:700">•••</span>
      </div>
      <div class="video-meta__divider"></div>

      <svg class="uploader__avatar" width="22" height="22" viewBox="0 0 22 22"><circle cx="11" cy="11" r="10" fill="none" stroke="#222" stroke-width="1.6"/><circle cx="11" cy="8.5" r="3.6" fill="#222"/><path d="M4.5 17a6.5 5.5 0 0 1 13 0z" fill="#222"/></svg>
      <span class="uploader__name">Your channel</span>
      <span class="uploader__subs">2158 subscriber</span>
      <span class="uploader__button">SUBSCRIBE</span>
      <p class="uploader__about" style="margin:0">Lorem ipsum dolor sit amet, consectetur adipiscing elit. Integer consectetur rhoncus pharetra. Proin posuere pellentesque maximus.</p>
    </div>
  </section>

  <section class="thumbnail">
    <div class="artwork" role="img" aria-label="Black and white engraving of a damaged castle among trees, with soldiers in helmets firing from a trench in the lower left and mounted officers on the right"></div>
    <h1 class="art-title" style="--size:60px;--lead:50px;--bottom:22px">
      <span>Nobody Expected</span><span>Such An Odd</span><span class="accent">Clash Ever</span>
    </h1>
  </section>
</main>
</body>
</html>
```